One pager Business Profile BrightCrew

We would like to create a onepage with our company profile. It is important to keep the basis like it is in the word document but make it nice and fancy. Consistancy in color and fonts is important.

I've added the logo so you can pick the correct colors. The small logo's you can reuse, I want to replace them once you are ready.

In the word document we used standard Word stuff, I would like nice symbols and a professional well designed block in the Cooperation part

I would like to have a source file so I can change (and translate) text, so better to use a regular font or free font (I need the font than).

Target Market(s)

Recruitment

Industry/Entity Type

Recruitment

Requirements
Must have
• a professional look

```html
<!DOCTYPE html>
<html lang="en">
<head>
<meta charset="utf-8">
<title>BrightCrew – Business Profile</title>
<link rel="stylesheet" href="https://fonts.googleapis.com/css2?family=Poppins:wght@400;500;600;700;800&family=Oswald:wght@500&display=swap">
<style>
:root{
  --navy:#123a5e;
  --navy-dark:#16365a;
  --blue:#1a7fd4;
  --sky:#35b5f0;
  --ink:#1d2733;
  --paper:#ffffff;
  --backdrop:#c6c6c6;
}
*{margin:0;padding:0;box-sizing:border-box}
html,body{width:682px;height:1200px;overflow:hidden}
body{background:var(--backdrop);font-family:"Poppins",sans-serif;color:var(--ink)}
.flyer{position:absolute;left:0;top:117px;width:682px;height:965px;background:var(--paper);overflow:hidden}
.abs{position:absolute}

.brand{left:41px;top:38px;font-size:21px;font-weight:500;letter-spacing:5px;color:var(--navy)}
.headline-top{left:40px;top:82px;font-size:30px;font-weight:700;color:var(--navy);letter-spacing:.3px}
.headline-main{left:37px;top:108px;font-size:66px;font-weight:800;color:var(--blue);letter-spacing:1px;line-height:1}
.dots{left:41px;top:181px;display:flex;gap:3px}
.dots span{width:6px;height:6px;border-radius:50%;background:var(--navy)}
.dots span:nth-child(3){background:#5f87ad}
.dots span:nth-child(4){background:#a9c3dc}
.tagline{left:41px;top:197px;font-size:17.5px;font-weight:500;line-height:1.2;color:var(--ink)}

.hero{left:0;top:0;width:682px;height:288px}

.band{left:0;top:288px;width:682px;height:36px;background:var(--navy-dark);color:#fff;font-size:11.8px;font-weight:700;display:flex;align-items:center;justify-content:center;letter-spacing:.1px}

.logo-cloud{left:0;top:324px;width:378px;height:217px;background:radial-gradient(ellipse at 50% 45%,#ffffff 0%,#eef0f3 55%,#dde1e6 100%)}
.stats{left:378px;top:324px;width:304px;height:217px;background:linear-gradient(135deg,#0f63c4 0%,#1a7fd4 50%,#2a9bec 100%)}
.stat-num{left:34px;top:34px;font-family:"Oswald",sans-serif;font-size:50px;font-weight:500;color:#fff;line-height:1}
.stat-text{left:90px;top:39px;width:184px;font-size:11px;line-height:12.5px;color:#fff}
.stat-rule{left:90px;top:106px;width:180px;height:1px;background:rgba(255,255,255,.35)}
.stars{left:34px;top:128px}
.stat-text2{left:90px;top:124px;width:176px;font-size:11px;line-height:12.5px;color:#fff}

.h2{font-size:21px;font-weight:700;line-height:1}
.offer-title{left:38px;top:565px;color:var(--navy)}
.offer-lead{left:38px;top:590px;width:284px;font-size:11px;font-weight:600;color:var(--blue);line-height:13px}
.offer-body{left:38px;top:637px;width:292px;font-size:9.6px;line-height:11px;color:var(--ink)}

.open-title{left:378px;top:565px;color:var(--blue)}
.open-list{left:378px;top:591px;width:272px;list-style:none;font-size:9.6px;line-height:11px;font-weight:500}
.open-list li{position:relative;padding-left:19px;margin-bottom:6px}
.open-list svg{position:absolute;left:0;top:1px}
.partner{left:380px;top:676px;width:280px;height:76px;border-left:2px solid var(--navy);padding-left:16px}
.partner h3{font-size:10.6px;font-weight:600;color:var(--blue);line-height:13px}
.partner p{margin-top:7px;font-size:9.4px;line-height:11px}

.teams{left:0;top:744px;width:354px;height:154px;background:var(--blue);border-radius:0 8px 8px 0;color:#fff}
.expertises{left:28px;top:20px;width:22px;height:114px;writing-mode:vertical-rl;transform:rotate(180deg);font-size:17px;font-weight:600;color:var(--navy-dark);text-align:center;letter-spacing:.5px}
.teams-title{left:72px;top:13px;font-size:19px;font-weight:700}
.team-col{list-style:none;font-size:10.4px;line-height:12px}
.team-col li{position:relative;padding-left:13px;margin-bottom:4px}
.team-col svg{position:absolute;left:0;top:2px}
.col-a{left:72px;top:44px;width:140px}
.col-b{left:221px;top:44px;width:130px}
.col-rule{left:208px;top:46px;width:0;height:92px;border-left:1px dashed rgba(255,255,255,.6)}

.coop-title{left:400px;top:776px;width:224px;text-align:center;font-size:13.5px;font-weight:700;color:var(--blue)}
.coop{left:378px;top:792px;width:270px;height:112px}

.footer-contact{left:38px;top:925px;display:flex;align-items:center;font-size:12.3px;font-weight:500;color:var(--navy)}
.footer-contact .sep{width:1px;height:17px;background:var(--navy);margin:0 12px}
.footer-contact svg{margin-right:4px}
.web{left:384px;top:917px;font-size:19.5px;font-weight:600;color:var(--navy);letter-spacing:1.6px}
.web span{color:var(--blue)}
</style>
</head>
<body>
<main class="flyer">

  <svg class="abs hero" viewBox="0 0 682 288" role="img" aria-label="Blue-toned city skyline photo with cloud computing icons">
    <defs>
      <linearGradient id="heroFill" x1="0" y1="0" x2="0" y2="1">
        <stop offset="0" stop-color="#1ab8f2"/>
        <stop offset=".55" stop-color="#1a86dc"/>
        <stop offset="1" stop-color="#1756b4"/>
      </linearGradient>
    </defs>
    <path d="M355 38 H682 V288 H0 V258 H270 Q308 258 312 226 L334 58 Q337 38 355 38 Z" fill="url(#heroFill)"/>
    <path d="M682 30 H355 Q331 30 328 54 L305 203" fill="none" stroke="#1a7fd4" stroke-width="1.6"/>
    <circle cx="305" cy="203" r="3.5" fill="#1a7fd4"/>
  </svg>

  <div class="abs brand">BRIGHTCREW</div>
  <div class="abs headline-top">BETTER EXPERTS</div>
  <div class="abs headline-main">FASTER</div>
  <div class="abs dots"><span></span><span></span><span></span><span></span></div>
  <div class="abs tagline">The best developers&nbsp; in<br>our network</div>

  <div class="abs band">WE OFFER OUR PROFESSIONALS ONLY IF&nbsp; WE ARE CONVINCED OF THEIR COMPETENCES AND SKILLS</div>

  <div class="abs logo-cloud" role="img" aria-label="Cloud of client company logos in coloured circles around a laptop"></div>

  <section class="abs stats">
    <div class="abs stat-num">15</div>
    <p class="abs stat-text">We have access to a&nbsp; specialist network of&nbsp; software development professionals carefully&nbsp; built up over a period of&nbsp; 15 years</p>
    <div class="abs stat-rule"></div>
    <svg class="abs stars" width="46" height="40" viewBox="0 0 46 40" aria-hidden="true">
      <polygon fill="#fff" points="9,0 11.3,6.2 18,6.4 12.8,10.5 14.6,17 9,13.2 3.4,17 5.2,10.5 0,6.4 6.7,6.2"/>
      <polygon fill="#fff" points="37,0 39.3,6.2 46,6.4 40.8,10.5 42.6,17 37,13.2 31.4,17 33.2,10.5 28,6.4 34.7,6.2"/>
      <polygon fill="#fff" points="23,14 25.9,21.6 34,21.9 27.6,26.9 29.8,34.8 23,30.2 16.2,34.8 18.4,26.9 12,21.9 20.1,21.6"/>
    </svg>
    <p class="abs stat-text2">By employing&nbsp; qualitatively suitable candidates, we receive positive customer&nbsp; reviews and score high customer satisfaction.</p>
  </section>

  <h2 class="abs h2 offer-title">OUR OFFER</h2>
  <p class="abs offer-lead">BrightCrew helps you solve your IT organisation's capacity problems by offering and deploying<br>high-quality, highly developed candidates.</p>
  <p class="abs offer-body">Our candidates, our professionals, are driven,&nbsp; and they are used to getting the best out of&nbsp; themselves and their project. They bring up-to-date&nbsp; knowledge for you, so they immediately tap the best level for you as a client to help achieve the objectives of the&nbsp; project, and therefore really complement your team. Our professionals are of immediate value and deliver&nbsp; demonstrable results..</p>

  <h2 class="abs h2 open-title">TRANSPARANT &amp; OPEN</h2>
  <ul class="abs open-list">
    <li><svg width="11" height="10" viewBox="0 0 11 10"><path d="M1 0 L11 5 L1 10 L4 5 Z" fill="#1a7fd4"/></svg>BrightCrew stands for transparency and openness, for both client and contractor.</li>
    <li><svg width="11" height="10" viewBox="0 0 11 10"><path d="M1 0 L11 5 L1 10 L4 5 Z" fill="#1a7fd4"/></svg>Clear agreements and no unnecessary obligations.</li>
    <li><svg width="11" height="10" viewBox="0 0 11 10"><path d="M1 0 L11 5 L1 10 L4 5 Z" fill="#1a7fd4"/></svg>Short lines, and smooth response times. For both the client and the professional.</li>
  </ul>
  <div class="abs partner">
    <h3>AS PART OF THE KESTREL GROUP AND<br>OUR PARTNER NETWORK,</h3>
    <p>BrightCrew is able to provide clients with full development teams, complete with test automators, scrum masters, product owners and business analysts and developers..</p>
  </div>

  <section class="abs teams">
    <div class="abs expertises">EXPERTISES</div>
    <h2 class="abs teams-title">TEAMS</h2>
    <ul class="abs team-col col-a">
      <li><svg width="9" height="9" viewBox="0 0 9 9"><rect x=".5" y=".5" width="8" height="8" rx="1.5" fill="none" stroke="#bfe0fa"/><path d="M2 4.6 L3.8 6.3 L7 2.6" fill="none" stroke="#fff" stroke-width="1.2"/></svg>Backend developers</li>
      <li><svg width="9" height="9" viewBox="0 0 9 9"><rect x=".5" y=".5" width="8" height="8" rx="1.5" fill="none" stroke="#bfe0fa"/><path d="M2 4.6 L3.8 6.3 L7 2.6" fill="none" stroke="#fff" stroke-width="1.2"/></svg>Frontend developers<br>(web frameworks)</li>
      <li><svg width="9" height="9" viewBox="0 0 9 9"><rect x=".5" y=".5" width="8" height="8" rx="1.5" fill="none" stroke="#bfe0fa"/><path d="M2 4.6 L3.8 6.3 L7 2.6" fill="none" stroke="#fff" stroke-width="1.2"/></svg>Software developers</li>
      <li><svg width="9" height="9" viewBox="0 0 9 9"><rect x=".5" y=".5" width="8" height="8" rx="1.5" fill="none" stroke="#bfe0fa"/><path d="M2 4.6 L3.8 6.3 L7 2.6" fill="none" stroke="#fff" stroke-width="1.2"/></svg>Data engineers</li>
      <li><svg width="9" height="9" viewBox="0 0 9 9"><rect x=".5" y=".5" width="8" height="8" rx="1.5" fill="none" stroke="#bfe0fa"/><path d="M2 4.6 L3.8 6.3 L7 2.6" fill="none" stroke="#fff" stroke-width="1.2"/></svg>Devops (cloud platforms)</li>
    </ul>
    <div class="abs col-rule"></div>
    <ul class="abs team-col col-b">
      <li><svg width="9" height="9" viewBox="0 0 9 9"><rect x=".5" y=".5" width="8" height="8" rx="1.5" fill="none" stroke="#bfe0fa"/><path d="M2 4.6 L3.8 6.3 L7 2.6" fill="none" stroke="#fff" stroke-width="1.2"/></svg>Web developers</li>
      <li><svg width="9" height="9" viewBox="0 0 9 9"><rect x=".5" y=".5" width="8" height="8" rx="1.5" fill="none" stroke="#bfe0fa"/><path d="M2 4.6 L3.8 6.3 L7 2.6" fill="none" stroke="#fff" stroke-width="1.2"/></svg>Testers(automation<br>&amp; functioneel)</li>
      <li><svg width="9" height="9" viewBox="0 0 9 9"><rect x=".5" y=".5" width="8" height="8" rx="1.5" fill="none" stroke="#bfe0fa"/><path d="M2 4.6 L3.8 6.3 L7 2.6" fill="none" stroke="#fff" stroke-width="1.2"/></svg>Mobile developers<br>(native apps)</li>
      <li><svg width="9" height="9" viewBox="0 0 9 9"><rect x=".5" y=".5" width="8" height="8" rx="1.5" fill="none" stroke="#bfe0fa"/><path d="M2 4.6 L3.8 6.3 L7 2.6" fill="none" stroke="#fff" stroke-width="1.2"/></svg>UX/UI developers</li>
    </ul>
  </section>

  <h2 class="abs coop-title">COOPERATION</h2>
  <svg class="abs coop" viewBox="0 0 270 112" font-family="Poppins, sans-serif">
    <g fill="#16365a">
      <path d="M22 14 Q22 4 32 4 H91 V52 H22 Z"/>
      <rect x="97" y="4" width="70" height="48" rx="3"/>
      <path d="M173 4 H231 Q241 4 241 14 V52 H173 Z"/>
      <rect x="22" y="58" width="219" height="48" rx="10"/>
    </g>
    <g fill="#fff" font-size="6.4" font-weight="600" text-anchor="middle">
      <text x="56" y="24">KESTREL</text><text x="56" y="32">GROUP</text>
      <text x="132" y="24">NETWERK</text><text x="132" y="32">PARTIJEN</text>
      <text x="207" y="28">KLANT</text>
    </g>
    <rect x="52" y="42" width="160" height="24" rx="12" fill="#1a7fd4" stroke="#fff" stroke-width="2"/>
    <text x="132" y="58.5" fill="#fff" font-size="12" font-weight="600" text-anchor="middle" letter-spacing=".4">BRIGHTCREW</text>
    <text x="132" y="92" fill="#fff" font-size="10" text-anchor="middle">ZZP'ers&#160; |&#160; developers</text>
    <g fill="none" stroke="#1a7fd4" stroke-width="1.3">
      <path d="M11 9 L14 5 L17 9 M11 13 L14 9 L17 13"/>
      <path d="M11 99 L14 103 L17 99 M11 95 L14 99 L17 95"/>
      <path d="M246 9 L249 5 L252 9 M246 13 L249 9 L252 13"/>
      <path d="M246 99 L249 103 L252 99 M246 95 L249 99 L252 95"/>
    </g>
    <text transform="translate(8 90) rotate(-90)" fill="#16365a" font-size="6.3" font-weight="600" letter-spacing=".2">CUSTOMER REQUEST</text>
    <text transform="translate(258 20) rotate(90)" fill="#16365a" font-size="6.3" font-weight="600" letter-spacing=".2">CUSTOMER REQUEST</text>
  </svg>

  <div class="abs footer-contact">
    <svg width="12" height="12" viewBox="0 0 24 24"><path d="M6.6 10.8a15 15 0 0 0 6.6 6.6l2.2-2.2a1 1 0 0 1 1-.25 11.4 11.4 0 0 0 3.6.57 1 1 0 0 1 1 1V20a1 1 0 0 1-1 1A17 17 0 0 1 3 4a1 1 0 0 1 1-1h3.5a1 1 0 0 1 1 1 11.4 11.4 0 0 0 .57 3.6 1 1 0 0 1-.25 1Z" fill="none" stroke="#1a7fd4" stroke-width="2.2"/></svg>
    <span>0031 30 555 01 23</span>
    <span class="sep"></span>
    <svg width="13" height="10" viewBox="0 0 13 10"><rect x=".6" y=".6" width="11.8" height="8.8" fill="#1a7fd4"/><path d="M.8 .8 L6.5 5.5 L12.2 .8" fill="none" stroke="#fff" stroke-width="1"/></svg>
    <span>info@brightcrew.nl</span>
  </div>
  <div class="abs web">www.<span>brightcrew</span>.nl</div>

</main>
</body>
</html>
```